Stationery for Villa Marenta Design Hotel**

Who we are:

Wander on an isolated beach while breathing in the fresh, salty, sea air. Listen to the warm Pacific wind rustling through green palm trees as you walk to a pristine lagoon. Feel the delicious warmth of the sun kiss your skin; the beach is yours. At Villa Marenta you can experience a vacation in undisturbed, natural beauty. We have created a place for you to find new strength, relaxation, and inner harmony. We offer total rest to the experienced traveler from all over the world.

We are a brand new and smartly built design-hotel (under construction) close to a unique beach and a fantastic surf spot in Huatulco, Southwest Mexico.

As you can see in the attachments, we do have an established corporate design, but as for now still need a format for booklets for information around our hotel and things to do in the area, important numbers (we fill in the content for that one).

Our corporate colors:
green #64b445, brown #b07043, blue #0ab7cf, yellow # f9b02a and #fcc01a, navy #444f69
Corporate fonts:
Krub and Miller Banner.
For further information access:
www.villamarenta.example
https://slidevault.example/view/QmPxLwZrTyKsNbVcHdJe/

Social Media: VillaMarenta

Industry/Entity Type

Hotel

Font styles to use
Other font styles liked:
• Krub, Miller Banner

Requirements
Must have
• Stick to Logo Design, defined corporate elements, logo, colors, fonts and general touch and feel
Nice to have
• Who we are:

Our corporate colors:
Corporate fonts:
Krub and Miller Banner.
www.villamarenta.example

Social Media: VillaMarenta

```html
<!DOCTYPE html>
<html lang="en">
<head>
<meta charset="utf-8">
<title>Villa Marenta Letterhead</title>
<link href="https://fonts.googleapis.com/css2?family=Krub:wght@400;500&family=Open+Sans:wght@400&display=swap" rel="stylesheet">
<style>
  :root {
    --backdrop: #e2e2e2;
    --paper: #f8f8f8;
    --ink: #4a4a4a;
    --gold: #e2a829;
    --green: #64b445;
    --brown: #b07043;
    --blue: #0ab7cf;
    --yellow: #f9b02a;
    --navy: #444f69;
  }
  * { box-sizing: border-box; margin: 0; padding: 0; }
  html, body {
    width: 1153px; height: 1200px; overflow: hidden;
    background: var(--backdrop);
  }
  .letterhead {
    position: absolute; left: 161px; top: 20px;
    width: 831px; height: 1160px;
    background: var(--paper);
    box-shadow: 0 10px 30px rgba(0,0,0,0.12);
  }
  .brand {
    position: absolute; left: 83px; top: 120px;
    display: flex; align-items: center; gap: 10px;
  }
  .brand-square {
    width: 24px; height: 24px; background: var(--gold);
  }
  .brand-name {
    font-family: "Krub", sans-serif; font-weight: 500;
    font-size: 21px; color: var(--gold);
  }
  .contact {
    position: absolute; left: 552px; top: 80px;
    font-family: "Krub", sans-serif; font-size: 16.5px;
    color: var(--ink); line-height: 21px;
  }
  .contact address { font-style: normal; margin-bottom: 5px; }
  .contact-line { display: flex; align-items: center; gap: 6px; line-height: 22px; }
  .contact-line svg { width: 16px; height: 16px; flex: none; }
  .letter {
    position: absolute; left: 75px; top: 298px; width: 680px;
    font-family: "Open Sans", sans-serif; font-size: 14.2px;
    line-height: 22.3px; color: var(--ink);
  }
  .letter p { margin-bottom: 22.3px; text-align: justify; }
  .letter p.salutation, .letter p.closing { text-align: left; }
  .signature {
    position: absolute; left: 75px; top: 889px;
    width: 97px; height: 91px;
    background: linear-gradient(135deg, #ececec, #e4e4e4);
  }
  .color-bands {
    position: absolute; left: 0; bottom: 0; width: 100%; height: 18px;
    display: flex; gap: 8px;
  }
  .color-bands span { flex: 1; }
  .band-green { background: var(--green); }
  .band-brown { background: var(--brown); }
  .band-blue { background: var(--blue); }
  .band-yellow { background: var(--yellow); }
  .band-navy { background: var(--navy); }
</style>
</head>
<body>
<main class="letterhead">
  <div class="brand">
    <span class="brand-square"></span>
    <span class="brand-name">Villa Marenta</span>
  </div>

  <div class="contact">
    <address>Playa Marenta, Huatulco<br>Oaxaca, Mexiko</address>
    <div class="contact-line">
      <svg viewBox="0 0 16 16"><path fill="#64b445" d="M3.6 1.2l2.3 2.6-1.3 1.9c.9 2 2.6 3.8 4.7 4.8l1.9-1.3 2.6 2.3-1.4 2.3C7.3 13.5 2.5 8.7 2.2 3.1z"/></svg>
      <span>+52 1 (555) 014 7392</span>
    </div>
    <div class="contact-line">
      <svg viewBox="0 0 16 16"><rect x="1" y="3" width="14" height="10" fill="#64b445"/><path d="M1.5 3.5L8 9l6.5-5.5" fill="none" stroke="#f8f8f8" stroke-width="1.2"/></svg>
      <span>hello@villamarenta.example</span>
    </div>
    <div class="contact-line">
      <svg viewBox="0 0 16 16" fill="none" stroke="#64b445" stroke-width="1.4"><circle cx="8" cy="8" r="6.5"/><path d="M2 6c3 1 5 0 7-3M4 13c1-3 4-4 10-3M6 2c2 3 4 7 4 12"/></svg>
      <span>www.villamarenta.example</span>
    </div>
  </div>

  <article class="letter">
    <p class="salutation">Dear customer,</p>
    <p>Lorem ipsum dolor sit amet, consectetur adipisicing elit, sed do eiusmod tempor incididunt ut labore et dolore magna aliqua. Ut enim ad minim veniam, quis nostrud exercitation ullamco laboris nisi ut aliquip ex ea commodo consequat. Duis aute irure dolor in reprehenderit in voluptate velit esse cillum dolore eu fugiat nulla pariatur. Excepteur sint occaecat cupidatat non proident, sunt in culpa qui officia deserunt mollit anim id est laborum.</p>
    <p>Lorem ipsum dolor sit amet, consectetur adipisicing elit, sed do eiusmod tempor incididunt ut labore et dolore magna aliqua. Ut enim ad minim veniam, quis nostrud exercitation ullamco laboris nisi ut aliquip ex ea commodo consequat. Duis aute irure dolor in reprehenderit in voluptate velit esse cillum dolore eu fugiat nulla pariatur. Excepteur sint occaecat cupidatat non proident, sunt in culpa qui officia deserunt mollit anim id est laborum.</p>
    <p>Lorem ipsum dolor sit amet, consectetur adipisicing elit, sed do eiusmod tempor incididunt ut labore et dolore magna aliqua. Ut enim ad minim veniam, quis nostrud exercitation ullamco laboris nisi ut aliquip ex ea commodo consequat. Duis aute irure dolor in reprehenderit in voluptate velit esse cillum dolore eu fugiat nulla pariatur. Excepteur sint occaecat cupidatat non proident, sunt in culpa qui officia deserunt mollit anim id est laborum.</p>
    <p>Lorem ipsum dolor sit amet, consectetur adipisicing elit, sed do eiusmod tempor incididunt ut labore et dolore magna aliqua. Ut enim ad minim veniam, quis nostrud exercitation ullamco laboris nisi ut aliquip ex ea commodo consequat. Duis aute irure dolor in reprehenderit.</p>
    <p class="closing">Yours Sincerely,</p>
  </article>

  <div class="signature" role="img" aria-label="Handwritten signature of the sender"></div>

  <div class="color-bands">
    <span class="band-green"></span>
    <span class="band-brown"></span>
    <span class="band-blue"></span>
    <span class="band-yellow"></span>
    <span class="band-navy"></span>
  </div>
</main>
</body>
</html>
```